MRT Property - Business Cards

Looking for a business card & general letterhead, signage etc design for our new logo.

Colours:
000a20
0056a2
00b5ef
0088ce
68cef2

Fonts:
Poppins
Karla

Please keep look and feel of new brand - example in the zip package I sent.

```html
<!DOCTYPE html>
<html lang="en">
<head>
<meta charset="utf-8">
<title>MRT Property – Business Cards</title>
<link rel="stylesheet" href="https://fonts.googleapis.com/css2?family=Poppins:wght@300;400;500;600;700&display=swap">
<style>
  :root {
    --navy-deep: #000a20;
    --card-bg: #0d1226;
    --blue-brand: #0056a2;
    --blue-mid: #0088ce;
    --blue-bright: #00b5ef;
    --blue-soft: #68cef2;
    --text-light: #e9edf5;
    --page-bg: #e4e6ea;
  }
  * { box-sizing: border-box; margin: 0; padding: 0; }
  html, body { width: 1200px; height: 780px; overflow: hidden; }
  body {
    background: var(--page-bg);
    font-family: "Poppins", sans-serif;
    display: flex;
    align-items: center;
    justify-content: center;
    gap: 50px;
  }
  .card {
    position: relative;
    width: 540px;
    height: 310px;
    border-radius: 22px;
    background: var(--card-bg);
    overflow: hidden;
    box-shadow: 0 10px 28px rgba(0, 10, 32, 0.25);
  }

  /* Front */
  .brand-name {
    position: absolute;
    left: 44px;
    top: 92px;
    font-size: 30px;
    font-weight: 600;
    color: var(--blue-brand);
    display: flex;
    align-items: center;
    gap: 12px;
    letter-spacing: 0.5px;
  }
  .brand-dot {
    width: 16px; height: 16px;
    border-radius: 50%;
    background: var(--blue-mid);
  }
  .divider {
    position: absolute;
    left: 290px;
    top: 44px;
    width: 1px;
    height: 150px;
    background: linear-gradient(to bottom, var(--blue-mid), rgba(0,136,206,0.35));
  }
  .person {
    position: absolute;
    left: 312px;
    top: 50px;
  }
  .person-name {
    font-size: 30px;
    line-height: 1.1;
    white-space: nowrap;
  }
  .person-name .first { color: var(--blue-brand); font-weight: 700; }
  .person-name .last { color: var(--blue-soft); font-weight: 400; }
  .person-role {
    font-size: 12px;
    font-weight: 500;
    color: var(--text-light);
    margin-top: 2px;
  }
  .contact-list {
    list-style: none;
    margin-top: 16px;
    font-size: 12.5px;
    font-weight: 300;
    color: var(--text-light);
  }
  .contact-list li {
    display: flex;
    align-items: center;
    gap: 8px;
    line-height: 22px;
  }
  .contact-list svg { width: 12px; height: 12px; flex: none; }
  .address {
    position: absolute;
    left: 44px;
    bottom: 26px;
    font-size: 12.5px;
    font-weight: 300;
    color: var(--text-light);
    white-space: nowrap;
  }

  /* Back */
  .back-pattern {
    position: absolute;
    inset: 0;
    background:
      radial-gradient(120% 110% at 100% 0%, rgba(0,136,206,0.55) 0%, rgba(0,86,162,0.35) 35%, rgba(13,18,38,0) 70%),
      var(--card-bg);
  }
  .back-brand {
    position: absolute;
    right: 36px;
    bottom: 30px;
    font-size: 15px;
    font-weight: 600;
    color: var(--blue-mid);
    display: flex;
    align-items: center;
    gap: 7px;
  }
  .back-brand .brand-dot { width: 9px; height: 9px; }
</style>
</head>
<body>

  <section class="card card-front">
    <div class="brand-name"><span class="brand-dot"></span>MRT Property</div>
    <div class="divider"></div>

    <div class="person">
      <p class="person-name"><span class="first">Callum</span> <span class="last">Reid</span></p>
      <p class="person-role">Director</p>
      <ul class="contact-list">
        <li>
          <svg viewBox="0 0 24 24" fill="var(--blue-bright)"><path d="M6.6 10.8a15.1 15.1 0 0 0 6.6 6.6l2.2-2.2c.3-.3.7-.4 1-.2 1.1.4 2.3.6 3.6.6.6 0 1 .4 1 1V20c0 .6-.4 1-1 1A17 17 0 0 1 3 4c0-.6.4-1 1-1h3.5c.6 0 1 .4 1 1 0 1.3.2 2.5.6 3.6.1.3 0 .7-.2 1z"/></svg>
          +61 2 9000 4815
        </li>
        <li>
          <svg viewBox="0 0 24 24" fill="none" stroke="var(--blue-bright)" stroke-width="2.2"><circle cx="12" cy="12" r="9"/><path d="M3 12h18M12 3c3 3.5 3 14.5 0 18M12 3c-3 3.5-3 14.5 0 18"/></svg>
          www.mrtproperty.com.au
        </li>
        <li>
          <svg viewBox="0 0 24 24" fill="none" stroke="var(--blue-bright)" stroke-width="2.2"><rect x="3" y="5" width="18" height="14" rx="2"/><path d="M3 7l9 6 9-6"/></svg>
          info@mrtproperty.com.au
        </li>
      </ul>
    </div>

    <p class="address">Suite 4.12, Level 4 18 Harbourline Road Rivergate NSW 2140</p>
  </section>

  <section class="card card-back">
    <div class="back-pattern" role="img" aria-label="Repeating brand symbol pattern fading from deep navy to bright blue toward the top right corner"></div>
    <div class="back-brand"><span class="brand-dot"></span>MRT Property</div>
  </section>

</body>
</html>
```